We need a business card for our gym. We are a PowerCore affiliate in Decatur Georgie established 2008. Our company name is Rally Functional Fitness. PowerCore Building Prime Fitness. Instagram and website is @rallygym. Hashtags we use #rallywithheart #madetorally We want something similar to the the black and neon green design attached but a different color scheme. No neon colors. Are company colors are the same as the blue and white card attached. We are open to ideas as far as colors however - just no neon.

Contact Information for Business Card

Rally Functional Fitness
472 Halvern Drive
Decatur GA 30041
Phone 404.555.0187 Website www.rallygym.example

Font styles to use
Other font styles liked:
• Futura Extra Bold Condensed

Colors

Designer to choose colors to be used in the design.

Requirements
Must have
• Our primary font we typically use for our name is Futura Extra Bold Condensed
Nice to have
• I attached a card from that is black and neon green from Zorva that we would like something similar. The blue and white is more similar to our colors. We also use have used black and white in the past. We use the chevrons as out logo. We are a PowerCore affiliate so I included a logo from them as well that may or may not be used on the card. Our instagram is @rallygym hashtags #madetorally #rallywithheart
Should not have
• No neon colors

```html
<!DOCTYPE html>
<html lang="en">
<head>
<meta charset="utf-8">
<title>Rally Functional Fitness – Business Card</title>
<link rel="stylesheet" href="https://fonts.googleapis.com/css2?family=Anton&family=Montserrat:wght@400;500&display=swap">
<style>
  :root {
    --brand-blue: #135c9a;
    --brand-blue-light: #3f7fb8;
    --card-white: #ffffff;
    --backdrop: #d2d2d2;
    --rule: #4a6db0;
    --shadow: rgba(0, 0, 0, 0.22);
  }
  * { box-sizing: border-box; margin: 0; padding: 0; }
  html, body { width: 1200px; height: 800px; overflow: hidden; }
  body {
    background: var(--backdrop);
    position: relative;
    font-family: "Montserrat", sans-serif;
  }
  .card {
    position: absolute;
    left: 300px;
    width: 600px;
    height: 343px;
    box-shadow: 0 4px 12px var(--shadow);
  }
  .card--back {
    top: 27px;
    background: var(--brand-blue);
    display: flex;
    align-items: center;
    justify-content: center;
  }
  .back-wordmark {
    font-family: "Anton", sans-serif;
    font-size: 84px;
    letter-spacing: 4px;
    color: var(--brand-blue-light);
    text-transform: uppercase;
    line-height: 1;
  }
  .card--front {
    top: 430px;
    background: var(--card-white);
    color: var(--brand-blue);
  }
  .wordmark {
    position: absolute;
    left: 48px;
    top: 96px;
    font-family: "Anton", sans-serif;
    text-transform: uppercase;
    color: var(--brand-blue);
    line-height: 1;
  }
  .wordmark__name { display: block; font-size: 96px; letter-spacing: 1px; }
  .wordmark__tagline { display: block; font-size: 25px; letter-spacing: 1px; margin-top: 6px; }
  .divider {
    position: absolute;
    left: 322px;
    top: 78px;
    width: 1px;
    height: 188px;
    background: var(--rule);
  }
  .contact {
    position: absolute;
    left: 348px;
    top: 74px;
    font-size: 15px;
    line-height: 1.3;
    color: var(--brand-blue);
  }
  .contact__name {
    font-family: "Anton", sans-serif;
    font-size: 22px;
    letter-spacing: 1px;
    text-transform: uppercase;
    word-spacing: 8px;
    line-height: 1.1;
  }
  .contact__role { text-transform: uppercase; margin-bottom: 14px; }
  .contact__address { margin-bottom: 14px; }
  .contact__line { display: flex; align-items: center; gap: 8px; }
  .contact__icon { width: 14px; height: 14px; flex: none; }
</style>
</head>
<body>
  <section class="card card--back" aria-label="Card back">
    <span class="back-wordmark">Rally</span>
  </section>

  <section class="card card--front" aria-label="Card front">
    <h1 class="wordmark">
      <span class="wordmark__name">Rally</span>
      <span class="wordmark__tagline">Functional Fitness</span>
    </h1>
    <div class="divider"></div>
    <div class="contact">
      <p class="contact__name">Marcus Tellwood</p>
      <p class="contact__role">Expert Coaches</p>
      <p class="contact__address">472 Halvern Drive<br>Decatur GA 30041</p>
      <p class="contact__line">
        <svg class="contact__icon" viewBox="0 0 24 24" aria-hidden="true"><path fill="currentColor" d="M6.6 10.8a15.1 15.1 0 0 0 6.6 6.6l2.2-2.2a1 1 0 0 1 1-.25 11.4 11.4 0 0 0 3.6.57 1 1 0 0 1 1 1V20a1 1 0 0 1-1 1A17 17 0 0 1 3 4a1 1 0 0 1 1-1h3.5a1 1 0 0 1 1 1c0 1.25.2 2.45.57 3.57a1 1 0 0 1-.25 1z"/></svg>
        404.555.0187
      </p>
      <p class="contact__line">
        <svg class="contact__icon" viewBox="0 0 24 24" aria-hidden="true"><circle cx="12" cy="12" r="10" fill="none" stroke="currentColor" stroke-width="2"/><path d="M2 12h20M12 2c3 3 3 17 0 20M12 2c-3 3-3 17 0 20" fill="none" stroke="currentColor" stroke-width="1.6"/></svg>
        www.rallygym.example
      </p>
    </div>
  </section>
</body>
</html>
```